Web Site Design For Real Estate Sales Project

The idea behind this project is pretty simple. I am putting my penthouse apartment up for sale and am trying to be creative in selling it.
Technically this will be pretty simple, it will be 3 pages but graphically this has to be as impressive as possible which is why I am trying Pixel Harbor.
The apartment is located in Barra Da Tijuca, Rio De Janeiro, Brazil. (This is where the 2016 Solstice Meet will be held)
I am looking for an index page and 2 sub-pages. I am open to all kinds of designs and navigation's but it has to make an impression quickly with a professional and enticing design. The index page should make it obvious that there is a penthouse apartment for sale in Barra Da Tijuca ( suburb of Rio De Janeiro). The first sub page is about the Condominium where the apartment is located, the second sub page is about the apartment itself.
Here is a more detailed description of what the 3 pages should be about.
Index Page
This is the landing page and should make it obvious that there is an apartment for sale in Barra Da Tijuca, Rio De Janeiro with the following attributes
251 SQ M
Duplex Penthouse
4 suites
Price R$ 2.200.000
Price per SQ M: R$ 8.764
First Sub-Page
This is about the Condominium which is called "Tranquil Cliff Suites" with the following bullets
*Family friendly and safe
*Direct access to the beach
*Many amenities like pool, football court, gym, sauna
There should be some photos of the condominium and a link to the site of the condominium ( www.tcsqv.com )
Second Sub-page
This is about the apartment. It should list in bullets the features of the apartment and then have a photo gallery of the view and various rooms. I have attached sample photos but will eventually have to use more photos.
Apartment Features
Price: R$ 2.220.000
251 m2 Duplex Penthouse
4 suites
maids room with bath
guest bathroom
living room
dinning room
Terrace with heated pool for year round use
Veranda
As mentioned above I am open to all designs and navigation so feel free to be creative. The important thing is catch peoples attention and get the message across in a few seconds, which is that there is an apartment for sale at this price with these features in this location. I will then use zintra clickreach and SEO to get people to the site.
Thanks
Men and Women from 30-60 years of age.
Apartment

```html
<!DOCTYPE html>
<html lang="en">
<head>
<meta charset="utf-8">
<title>Skyhome Serra — Apartment for Sale in Barra da Tijuca</title>
<link href="https://fonts.googleapis.com/css2?family=Oswald:wght@400;500;600&family=Open+Sans:wght@400&display=swap" rel="stylesheet">
<style>
  :root {
    --orange: #ff9d0a;
    --orange-text: #ffa514;
    --nav-ink: #1c1408;
    --nav-light: #fff3d6;
    --white: #ffffff;
    --panel: rgba(0, 0, 0, 0.86);
    --sky-top: #1f4fa3;
    --sky-mid: #4f7fc0;
    --sea: #1d3f78;
    --land: #5a5a3c;
    --hill: #2e3a16;
  }
  * { margin: 0; padding: 0; box-sizing: border-box; }
  html, body { width: 1200px; height: 878px; overflow: hidden; }
  body { position: relative; font-family: "Oswald", "Arial Narrow", sans-serif; color: var(--white); background: #000; }

  .scenery {
    position: absolute; inset: 0;
    background:
      linear-gradient(180deg, rgba(0,0,0,0) 0%, rgba(0,0,0,0) 70%, rgba(40,50,20,0.9) 100%),
      linear-gradient(180deg, var(--sky-top) 0%, var(--sky-mid) 28%, #9fb2c9 38%, var(--sea) 46%, var(--land) 70%, var(--hill) 100%);
  }

  .shapes { position: absolute; inset: 0; }

  .brand {
    position: absolute; left: 470px; top: 68px; width: 260px;
    text-align: center; color: var(--white); font-weight: 600; line-height: 1;
  }
  .brand-name { font-size: 62px; letter-spacing: -1px; }
  .brand-domain { font-size: 28px; margin-top: 6px; letter-spacing: 1px; }

  .main-nav { position: absolute; left: 0; top: 250px; width: 1200px; height: 44px; }
  .nav-link {
    position: absolute; top: 0; font-size: 34px; font-weight: 500;
    letter-spacing: -1px; line-height: 44px; text-decoration: none; color: var(--nav-light);
    text-shadow: 0 1px 2px rgba(120,60,0,0.45);
  }
  .nav-link.is-active { color: var(--nav-ink); text-shadow: none; }
  .nav-home { left: 299px; }
  .nav-suites { left: 408px; }
  .nav-about { left: 733px; }

  .headline { position: absolute; left: 303px; top: 384px; line-height: 1; }
  .headline-main { font-size: 58px; font-weight: 500; letter-spacing: -2px; color: var(--white); }
  .headline-sub { font-size: 46px; font-weight: 500; letter-spacing: -1.5px; color: var(--orange-text); margin-top: 2px; }

  .features { position: absolute; left: 186px; top: 560px; list-style: none; }
  .features li {
    position: relative; padding-left: 34px; font-size: 38px; font-weight: 400;
    letter-spacing: -1px; line-height: 48px;
  }
  .features li::before {
    content: ""; position: absolute; left: 0; top: 18px; width: 13px; height: 13px; background: var(--orange);
  }

  .pricing { position: absolute; left: 593px; top: 566px; line-height: 1; }
  .price-row { white-space: nowrap; letter-spacing: -1.5px; font-weight: 500; }
  .price-row + .price-row { margin-top: 2px; }
  .price-label { font-size: 40px; color: var(--orange-text); }
  .price-currency { font-size: 60px; color: var(--orange-text); }
  .price-value { font-size: 60px; color: var(--white); }

  .site-footer {
    position: absolute; left: 0; width: 1200px; top: 766px; text-align: center;
    font-family: "Open Sans", Arial, sans-serif; font-size: 10.5px; color: var(--white);
  }
  .social { position: absolute; left: 961px; top: 758px; display: flex; gap: 4px; }
  .social-dot { width: 22px; height: 22px; border: 2px solid var(--white); border-radius: 50%; }
</style>
</head>
<body>
  <div class="scenery" role="img" aria-label="Aerial photograph of Barra da Tijuca coastline, beach, lagoons and green hills under a blue sky"></div>

  <svg class="shapes" width="1200" height="878" viewBox="0 0 1200 878" aria-hidden="true">
    <!-- navigation ribbon -->
    <polygon points="171,304 223,257 293,347" fill="var(--white)"/>
    <polygon points="1011,210 985,300 1027,339" fill="var(--white)"/>
    <polygon points="189,210 1011,210 977,336 274,336" fill="var(--orange)"/>
    <line x1="382" y1="258" x2="382" y2="286" stroke="#ffd08a" stroke-width="1" stroke-dasharray="2 2"/>
    <line x1="705" y1="258" x2="705" y2="286" stroke="#ffd08a" stroke-width="1" stroke-dasharray="2 2"/>
    <!-- headline band -->
    <rect x="171" y="374" width="858" height="3" fill="#0b1a33" opacity="0.85"/>
    <rect x="171" y="380" width="858" height="132" fill="var(--panel)"/>
    <rect x="171" y="512" width="858" height="5" fill="var(--white)"/>
    <polygon points="575,517 625,517 600,541" fill="var(--white)"/>
    <rect x="171" y="532" width="858" height="3" fill="#0b1a33" opacity="0.85"/>
    <!-- details panel -->
    <rect x="171" y="538" width="858" height="192" fill="var(--panel)"/>
    <!-- brace -->
    <path d="M510 564 C 522 564, 522 572, 522 582 L 522 614 C 522 622, 526 627, 535 628 C 526 629, 522 634, 522 642 L 522 674 C 522 684, 522 692, 510 692"
          fill="none" stroke="var(--white)" stroke-width="2.5"/>
  </svg>

  <div class="brand" aria-label="Skyhome Serra.com">
    <div class="brand-name">SKYHOME</div>
    <div class="brand-domain">SERRA.COM</div>
  </div>

  <nav class="main-nav">
    <a class="nav-link nav-home is-active" href="#">HOME</a>
    <a class="nav-link nav-suites" href="#">TRANQUIL CLIFF SUITES</a>
    <a class="nav-link nav-about" href="#">ABOUT APARTMENT</a>
  </nav>

  <header class="headline">
    <h1 class="headline-main">APARTMENT FOR SALE</h1>
    <h2 class="headline-sub">IN BARRA DA TIJUCA, RIO DE JANEIRO</h2>
  </header>

  <ul class="features">
    <li>251 SQ M</li>
    <li>Duplex Penthouse</li>
    <li>4 suites</li>
  </ul>

  <div class="pricing">
    <p class="price-row"><span class="price-label">Price </span><span class="price-currency">R</span><span class="price-value">$ 2.200.000</span></p>
    <p class="price-row"><span class="price-label">Price per SQ M: </span><span class="price-currency">R</span><span class="price-value">$ 8.764</span></p>
  </div>

  <footer class="site-footer">© 2013 skyhome-serra.com. All rights reserved.</footer>
  <div class="social" aria-label="Social links">
    <span class="social-dot"></span>
    <span class="social-dot"></span>
  </div>
</body>
</html>
```